Electric mountain bike tours nz

We are an Electric Mountain bike tour company in New Zealand. We will be offering bike rental and guided tours around the Nelson region in New Zealand. I want our website to represent both Mountain biking and New Zealand with the colours layout and features. We want tabs for the following:
-1 about us
-2 what we offer
-3 bookings/contact
Under the about us tab will be who we are as a a company. I want the ability to add videos to each of these tabs as we move foward with videos of the tracks we will be riding. I want the website to be editable so I can add and remove videos/photos myself. Also "our bikes" will be under this tab.
Under the what we offer tab will be
-1 bike rental and pricing
-2 guided tours and pricing
-3 recommended package deals.
I want to able to put the tracks under the guided tours tab and select beginner/ intermediate/advanced and have the tracks in each of the following to match the rider level. Also to be able to have a small video of the track would be great in this section.
Bookings and contact tab
(Further information for this tab to be updated soon)
Coded - Design and coding required
1 page
- Silver ferns, kiwi, mountains

```html
<!DOCTYPE html>
<html lang="en">
<head>
<meta charset="utf-8">
<title>Ferntrack – Electric Mountain Bike Tours</title>
<link href="https://fonts.googleapis.com/css2?family=Montserrat:wght@400;600;700;800&family=Open+Sans:wght@400;600&display=swap" rel="stylesheet">
<style>
:root{
  --red:#c8102e;
  --navy:#1d2c78;
  --navy-deep:#131d55;
  --ink:#2b2b2b;
  --muted:#777;
  --white:#fff;
  --line:#d8d8d8;
  --footer:#1c1c1c;
}
*{box-sizing:border-box;margin:0;padding:0}
html,body{width:1200px;height:3168px;overflow:hidden}
body{position:relative;background:var(--white);font-family:"Open Sans",Arial,sans-serif;color:var(--ink)}
.abs{position:absolute}
h2{font-family:"Montserrat",Arial,sans-serif;font-weight:700;text-transform:uppercase}

/* hero */
.hero{left:0;top:0;width:1200px;height:650px;background:linear-gradient(160deg,#3c4a2a 0%,#5d6b3a 35%,#7a6a48 65%,#a88a62 100%)}
.brand{left:130px;top:26px;display:flex;align-items:center;gap:12px;font-family:"Montserrat",sans-serif;font-weight:800;font-size:30px;color:var(--white);letter-spacing:1px}
.brand-mark{width:22px;height:22px;border-radius:50%;background:var(--white)}
.nav{right:130px;top:28px;display:flex;gap:34px;list-style:none}
.nav li{font-family:"Montserrat",sans-serif;font-size:15px;font-weight:600;color:var(--white);text-transform:uppercase}
.arrow{top:300px;color:var(--white);font-size:40px;font-family:"Montserrat",sans-serif}
.edge{left:0;width:1200px}

/* welcome */
.welcome-title{left:130px;top:738px;font-size:30px;color:var(--red)}
.welcome-text{left:130px;top:790px;width:470px;font-size:14px;line-height:21px;color:var(--muted)}
.video{left:640px;top:745px;width:430px;height:200px;background:linear-gradient(135deg,#3d4e3b,#6c7a64 50%,#2c3a4b)}
.play{left:835px;top:825px;width:42px;height:42px;border-radius:50%;background:var(--white)}
.play::after{content:"";position:absolute;left:16px;top:12px;border-left:14px solid #222;border-top:9px solid transparent;border-bottom:9px solid transparent}

/* services */
.band{left:0;width:1200px;background:linear-gradient(180deg,var(--navy) 0%,var(--navy-deep) 100%)}
.section-title{left:0;width:1200px;text-align:center;font-size:30px}
.on-dark{color:var(--white)}
.card{top:1240px;width:300px;height:265px;background:var(--white);text-align:center;padding:30px 24px 0}
.card svg{width:54px;height:54px}
.card h3{font-family:"Montserrat",sans-serif;font-weight:700;font-size:22px;line-height:26px;text-transform:uppercase;margin:14px 0 14px;color:#222}
.card p{font-size:12.5px;line-height:18px;color:var(--muted)}

/* bikes */
.bikes-title{top:1730px;color:var(--red)}
.bike{top:1800px;width:400px;height:250px;background:radial-gradient(ellipse at center,#6b6b6b 0%,#2e2e2e 55%,#fff 72%)}
.bike-name{top:2075px;width:400px;text-align:center;font-size:17px;color:#333}

/* bookings */
.booking-form{left:130px;top:2400px;width:940px}
.row{display:flex;gap:20px;margin-bottom:18px}
.field{flex:1;height:38px;background:var(--white);font-size:12px;color:#888;padding:0 12px;display:flex;align-items:center;justify-content:space-between}
.field.tall{height:40px}
.submit{display:block;margin:30px auto 0;width:76px;height:34px;background:var(--red);color:var(--white);font-family:"Montserrat",sans-serif;font-weight:700;font-size:13px;border:0}

/* contact */
.contact-title{top:2845px;color:var(--red)}
.contact-line{left:0;top:2898px;width:1200px;display:flex;justify-content:center;gap:22px;font-size:22px;color:#222;align-items:center}
.contact-line span{display:flex;align-items:center;gap:8px}

/* footer */
.footer{left:0;top:2980px;width:1200px;height:188px;background:var(--footer)}
.footer-nav{left:130px;top:3090px;display:flex;gap:18px;list-style:none;font-size:12px;color:#bbb}
.copyright{left:130px;top:3120px;font-size:11px;color:#888}
.social{right:130px;top:3088px;display:flex;gap:14px}
.social span{width:22px;height:22px;background:#bbb;border-radius:3px}
</style>
</head>
<body>

<header class="hero abs" role="img" aria-label="Photo of an electric mountain bike parked beside a trail marker on a forest track"></header>
<div class="brand abs"><span class="brand-mark"></span>FERNTRACK</div>
<ul class="nav abs">
  <li>Home</li><li>About Us</li><li>What We Offer</li><li>Bookings</li><li>Contact Us</li>
</ul>
<div class="arrow abs" style="left:52px">‹</div>
<div class="arrow abs" style="right:52px">›</div>
<svg class="edge abs" style="top:590px" width="1200" height="62" viewBox="0 0 1200 62">
  <polygon fill="#fff" points="0,30 60,8 110,34 180,4 250,38 320,12 400,40 470,6 540,36 620,14 700,42 770,10 840,38 920,6 990,34 1060,12 1130,40 1200,16 1200,62 0,62"/>
</svg>

<section>
  <h2 class="welcome-title abs">Welcome to Ferntrack</h2>
  <p class="welcome-text abs">We are a small crew of riders based in Nelson, New Zealand, sharing the trails we love on quality electric mountain bikes. Whether you want to explore on your own with a rental or follow a local guide through native bush and along ridge lines, we match every ride to your level. Our tours cover beginner, intermediate and advanced tracks, with clear briefings, well maintained bikes and plenty of time to stop and take in the views across Tasman Bay.</p>
  <div class="video abs" role="img" aria-label="Video still of riders on a ridge overlooking the bay"></div>
  <div class="play abs"></div>
</section>

<section>
  <div class="band abs" style="top:930px;height:720px" role="img" aria-label="Blue-toned photo of mountains and a coastal bay"></div>
  <svg class="edge abs" style="top:920px" width="1200" height="90" viewBox="0 0 1200 90">
    <polygon fill="#fff" points="0,0 1200,0 1200,40 1130,20 1070,60 1000,30 930,70 860,18 790,56 720,24 650,66 580,14 510,52 440,22 370,64 300,20 230,58 160,26 90,62 0,24"/>
  </svg>
  <h2 class="section-title on-dark abs" style="top:1178px">Our Services</h2>
  <div class="card abs" style="left:130px">
    <svg viewBox="0 0 54 54" fill="none" stroke="#444" stroke-width="2"><path d="M10 26 L28 8 H46 V26 L28 44 Z"/><circle cx="38" cy="16" r="3"/></svg>
    <h3>Bike Rental and Pricing</h3>
    <p>Half day and full day hire on fully serviced e-bikes, with helmets, maps and trail advice included in every rental.</p>
  </div>
  <div class="card abs" style="left:450px">
    <svg viewBox="0 0 54 54" fill="none" stroke="#444" stroke-width="2"><rect x="12" y="6" width="30" height="40" rx="2"/><circle cx="27" cy="22" r="7"/><path d="M22 34 H32 M20 40 H34"/></svg>
    <h3>Guided Tours and Pricing</h3>
    <p>Ride with a local guide on tracks sorted by level, from gentle beginner loops to technical advanced descents.</p>
  </div>
  <div class="card abs" style="left:770px">
    <svg viewBox="0 0 54 54" fill="none" stroke="#444" stroke-width="2"><rect x="6" y="10" width="24" height="34" rx="2"/><rect x="24" y="6" width="24" height="40" rx="2"/></svg>
    <h3>Recommended Package Deals</h3>
    <p>Bundles that pair bike hire, guided rides and local stays so you can plan a full trip in one booking.</p>
  </div>
  <svg class="edge abs" style="top:1590px" width="1200" height="70" viewBox="0 0 1200 70">
    <polygon fill="#fff" points="0,70 1200,70 1200,20 1120,50 1050,10 980,44 910,6 840,48 770,16 700,52 630,12 560,46 490,8 420,50 350,18 280,54 210,14 140,46 70,10 0,40"/>
  </svg>
</section>

<section>
  <h2 class="section-title bikes-title abs">Our Electric Mountain Bikes</h2>
  <div class="bike abs" style="left:125px" role="img" aria-label="Side view of a black full suspension electric mountain bike"></div>
  <div class="bike abs" style="left:675px" role="img" aria-label="Side view of a silver full suspension electric mountain bike"></div>
  <p class="bike-name abs" style="left:125px">Vestibulum condimentum</p>
  <p class="bike-name abs" style="left:675px">Etiam mattis</p>
</section>

<section>
  <div class="band abs" style="top:2200px;height:590px" role="img" aria-label="Blue-toned aerial photo of forest trails and hills"></div>
  <svg class="edge abs" style="top:2190px" width="1200" height="80" viewBox="0 0 1200 80">
    <polygon fill="#fff" points="0,0 1200,0 1200,44 1130,16 1060,56 990,22 920,62 850,14 780,50 710,20 640,60 570,12 500,48 430,20 360,58 290,16 220,52 150,18 80,56 0,20"/>
  </svg>
  <h2 class="section-title on-dark abs" style="top:2338px">Bookings</h2>
  <form class="booking-form abs">
    <div class="row"><div class="field">Name</div><div class="field">Email</div><div class="field">Phone</div><div class="field">City</div></div>
    <div class="row"><div class="field">Number of People <span>▾</span></div><div class="field">Start Date <span>▦</span></div><div class="field">End Date <span>▦</span></div><div class="field">Package Type <span>▾</span></div></div>
    <div class="row"><div class="field tall">Message</div></div>
    <button class="submit" type="button">SUBMIT</button>
  </form>
  <svg class="edge abs" style="top:2730px" width="1200" height="70" viewBox="0 0 1200 70">
    <polygon fill="#fff" points="0,70 1200,70 1200,18 1130,48 1060,12 990,50 920,8 850,44 780,14 710,52 640,10 570,46 500,16 430,54 360,12 290,48 220,10 150,50 80,16 0,42"/>
  </svg>
</section>

<section>
  <h2 class="section-title contact-title abs">Contact Us</h2>
  <div class="contact-line abs">
    <span><svg width="20" height="20" viewBox="0 0 24 24" fill="#222"><path d="M6.6 10.8a15 15 0 0 0 6.6 6.6l2.2-2.2a1 1 0 0 1 1-.25 11.4 11.4 0 0 0 3.6.57 1 1 0 0 1 1 1V20a1 1 0 0 1-1 1A17 17 0 0 1 3 4a1 1 0 0 1 1-1h3.5a1 1 0 0 1 1 1c0 1.25.2 2.45.57 3.6a1 1 0 0 1-.25 1z"/></svg>021 555 0143</span>
    <span style="color:#999">/</span>
    <span><svg width="20" height="16" viewBox="0 0 24 18" fill="#222"><path d="M0 0h24v18H0z M2 2v1l10 7 10-7V2z" fill-rule="evenodd"/></svg>info@ferntrack.co.nz</span>
  </div>
</section>

<footer>
  <div class="footer abs"></div>
  <svg class="edge abs" style="top:2968px" width="1200" height="60" viewBox="0 0 1200 60">
    <polygon fill="#fff" points="0,0 1200,0 1200,30 1140,12 1080,44 1010,16 940,50 870,10 800,42 730,18 660,52 590,12 520,44 450,16 380,50 310,14 240,46 170,12 100,48 0,18"/>
  </svg>
  <ul class="footer-nav abs"><li>Home</li><li>About Us</li><li>What We Offer</li><li>Bookings</li><li>Contact</li></ul>
  <p class="copyright abs">Copyright © 2024 Ferntrack. All rights reserved.</p>
  <div class="social abs"><span></span><span></span><span></span><span></span></div>
</footer>

</body>
</html>
```